MRT Property - Business Cards

Looking for a business card & general letterhead, signage etc design for our new logo.

Colours:
000a20
0056a2
00b5ef
0088ce
68cef2

Fonts:
Poppins
Karla

Please keep look and feel of new brand - example in the zip package I sent.

```html
<!DOCTYPE html>
<html lang="en">
<head>
<meta charset="utf-8">
<title>MRT Property – Business Cards</title>
<link rel="stylesheet" href="https://fonts.googleapis.com/css2?family=Poppins:wght@600;700&family=Karla:wght@400;700&display=swap">
<style>
  :root{
    --ink:#000a20;
    --navy:#0f1428;
    --brand-blue:#0056a2;
    --cyan:#00b5ef;
    --mid-blue:#0088ce;
    --sky:#68cef2;
    --stage:#3d3d3d;
    --white:#ffffff;
  }
  *{box-sizing:border-box;margin:0;padding:0}
  html,body{width:1200px;height:803px;overflow:hidden}
  body{background:var(--stage);display:flex;align-items:center;justify-content:center;gap:40px;font-family:"Karla",sans-serif}
  .card{width:540px;height:309px;border-radius:18px;position:relative;border-bottom:2px solid var(--sky);box-shadow:0 14px 30px rgba(0,0,0,.35)}
  .card-front{background:var(--brand-blue);color:var(--white);padding:34px 36px}
  .card-back{background:var(--navy);display:flex;align-items:center;justify-content:center}
  .wordmark{font-family:"Poppins",sans-serif;font-weight:700;letter-spacing:.02em;line-height:1}
  .card-front .wordmark{font-size:28px;color:var(--white)}
  .card-back .brand{display:flex;align-items:center;gap:14px}
  .card-back .brand-dot{width:34px;height:34px;border-radius:50%;background:var(--cyan)}
  .card-back .wordmark{font-size:44px;color:var(--brand-blue)}
  .person{margin-top:22px}
  .person-name{font-family:"Poppins",sans-serif;font-weight:700;font-size:20px;line-height:1.1}
  .person-title{font-size:12px;opacity:.9}
  .address{margin-top:14px;font-size:12.5px;line-height:1.35}
  .contacts{margin-top:12px;list-style:none;font-size:12.5px;line-height:1.45}
  .contacts li{display:flex;align-items:center;gap:8px}
  .contacts svg{width:11px;height:11px;flex:none;fill:var(--white)}
</style>
</head>
<body>
  <section class="card card-front">
    <div class="wordmark">MRT Property</div>
    <div class="person">
      <div class="person-name">Daniel Reyes</div>
      <div class="person-title">President</div>
    </div>
    <address class="address" style="font-style:normal">
      4120 Harbour View Road<br>Halifax, Canada 20418
    </address>
    <ul class="contacts">
      <li><svg viewBox="0 0 12 12" aria-hidden="true"><path d="M2.5 1h2l1 3-1.3 1a7 7 0 0 0 2.8 2.8L8 6.5l3 1v2a1.5 1.5 0 0 1-1.5 1.5A8.5 8.5 0 0 1 1 2.5 1.5 1.5 0 0 1 2.5 1z"/></svg>555-210-4781</li>
      <li><svg viewBox="0 0 12 12" aria-hidden="true"><path d="M3.5 0h5A1 1 0 0 1 9.5 1v10a1 1 0 0 1-1 1h-5a1 1 0 0 1-1-1V1a1 1 0 0 1 1-1zm.5 1.5v7.5h4V1.5z"/></svg>555-384-9062</li>
      <li><svg viewBox="0 0 12 12" aria-hidden="true"><path d="M0 2h12v8H0zm1.3 1.2L6 6.5l4.7-3.3z"/></svg>info@MRTproperty.com</li>
      <li><svg viewBox="0 0 12 12" aria-hidden="true"><circle cx="6" cy="6" r="6"/></svg>www.MRTproperty.com</li>
    </ul>
  </section>

  <section class="card card-back">
    <div class="brand">
      <span class="brand-dot"></span>
      <span class="wordmark">MRT Property</span>
    </div>
  </section>
</body>
</html>
```